Brindleworth.com -> We need someone to design a homepage [For Mobile]

We need a graphic design of our homepage for mobile, which will include login and signup. It's only the design we need, we would take care of the coding, so if you're a good designer you're welcome to participate. The Login & Registration page contain a few fields. Login --> Username & Password & Forgot my Password. Registration --> Email, Username, Password. Needs to be a clean design.[Registration in a different page, Login and Homepage in the same one]
Updates

Project Deadline Extended Reason: We're going to consider what we got so far and allow others to submit more designs as well, the final deadline would be this week, we won't extend it again. Added Saturday, December 20, 2014

Project Deadline Extended Reason: Very sorry, we just got more than expected designs and we want to go over all of them in order to make a proper decision - we would extend the project until the 1st of January 2015, this is definitely a FINAL date. Added Friday, December 26, 2014

Industry/Entity Type

Graphic Design

Number of Pages Required

2 page

Requirements
Must have
• * Enclosed our logo to include with the design.
• * Add the following text as well
• WANT TO EARN EXTRA MONEY?
• WITH BRINDLEWORTH.COM YOU CAN!
• BRINDLEWORTH.COM. IT'S AS EASY AS 1, 2, 3.
• (1) Register (2) Earn & Win Coins (3) Redeem Coins
• * It must have "Login" and "Register" buttons on the home page.
Nice to have
• [Note: Also to make it easier for you, enclosed a screenshot of the main page in a desktop (PC) view.]

```html
<!DOCTYPE html>
<html lang="en">
<head>
<meta charset="utf-8">
<title>Brindleworth.com – Mobile Home</title>
<link href="https://fonts.googleapis.com/css2?family=Kalam:wght@700&family=Lato:wght@400;700&display=swap" rel="stylesheet">
<style>
  :root{
    --page:#e6e6e6;
    --bar:#231f1e;
    --sky-top:#6a829d;
    --sky-mid:#3b4557;
    --sky-low:#262a38;
    --panel:rgba(40,46,60,.55);
    --yellow:#e9c12e;
    --orange:#d9531a;
    --green:#8bc43f;
    --white:#ffffff;
    --field-text:#555b66;
    --icon:#4a6aa8;
    --button:#4762a4;
    --link:#d7dfea;
  }
  *{box-sizing:border-box;margin:0;padding:0}
  html,body{width:1120px;height:1200px;overflow:hidden}
  body{background:var(--page);font-family:"Lato",sans-serif;position:relative}
  .screen{position:absolute;left:240px;top:35px;width:640px;height:1130px;background:var(--bar);overflow:hidden}
  .status-bar{height:66px;display:flex;align-items:center;justify-content:space-between;padding:0 20px;color:var(--white);font-size:23px;position:relative}
  .status-bar .time{position:absolute;left:0;right:0;text-align:center;pointer-events:none}
  .signal{display:flex;align-items:center;gap:10px}
  .dots{letter-spacing:1px;font-size:18px}
  .battery{display:flex;align-items:center;gap:8px}
  .content{position:absolute;left:16px;right:16px;top:66px;bottom:16px;
    background:linear-gradient(180deg,var(--sky-top) 0%,var(--sky-mid) 55%,var(--sky-low) 88%,#1f2130 100%)}
  .brand{position:absolute;top:78px;left:0;right:0;display:flex;justify-content:center;align-items:center;gap:14px}
  .brand-dot{width:30px;height:30px;border-radius:50%;background:var(--green)}
  .brand-name{font-weight:700;font-size:34px;color:var(--white)}
  .headline{position:absolute;top:184px;left:0;right:0;text-align:center;font-family:"Kalam",cursive;font-weight:700;font-size:38px;color:var(--white)}
  .headline .earn{color:var(--yellow)}
  .headline .extra{color:var(--orange)}
  .headline .money{color:var(--green)}
  .tagline{position:absolute;top:238px;left:0;right:0;text-align:center;color:var(--white);font-size:24px}
  .coin-art{position:absolute;left:71px;top:325px;width:440px;height:420px;border-radius:16px;
    background:linear-gradient(180deg,rgba(110,140,30,.55) 0%,rgba(90,120,25,.45) 60%,rgba(60,80,30,0) 100%)}
  .panel{position:absolute;left:69px;width:470px;background:var(--panel);border-radius:12px}
  .steps{top:281px;height:321px}
  .login{top:632px;height:360px}
  .step{position:absolute;left:43px;width:360px;height:72px}
  .step-bar{position:absolute;left:55px;top:8px;width:303px;height:57px;display:flex;align-items:center;padding-left:32px;
    color:var(--white);font-size:14px;font-weight:700;text-transform:uppercase;border:2px solid rgba(255,255,255,.35)}
  .step-num{position:absolute;left:0;top:0;width:72px;height:72px;border-radius:50%;border:5px solid var(--white);
    display:flex;align-items:center;justify-content:center;color:var(--white);font-size:32px}
  .step.one{top:56px}.step.two{top:144px}.step.three{top:233px}
  .one .step-bar,.one .step-num{background:var(--yellow)}
  .two .step-bar,.two .step-num{background:var(--orange)}
  .three .step-bar,.three .step-num{background:var(--green)}
  .field{position:absolute;left:52px;width:359px;height:57px;background:var(--white);display:flex;align-items:center;padding-left:28px;gap:28px;
    color:var(--field-text);font-size:15px}
  .field.user{top:40px}.field.pass{top:115px}
  .login-row{position:absolute;left:52px;top:190px;width:359px;height:46px;display:flex;align-items:center;justify-content:space-between}
  .login-btn{width:150px;height:46px;background:var(--green);color:var(--white);font-weight:700;font-size:16px;
    text-transform:uppercase;display:flex;align-items:center;justify-content:center;border-radius:3px}
  .forgot{color:var(--link);font-size:15px;text-decoration:underline}
  .social-btn{position:absolute;left:96px;top:262px;width:279px;height:54px;background:var(--button);border-radius:3px;
    display:flex;align-items:center;gap:16px;padding-left:14px;color:var(--white);font-size:22px}
  .social-mark{width:26px;height:26px;background:var(--white);opacity:.9;border-radius:3px}
</style>
</head>
<body>
  <div class="screen">
    <div class="status-bar">
      <div class="signal"><span class="dots">●●●○○</span><span>KESTREL</span>
        <svg width="22" height="16" viewBox="0 0 22 16"><path d="M1 5a14 14 0 0 1 20 0M4.5 8.5a9 9 0 0 1 13 0M8 12a4 4 0 0 1 6 0" fill="none" stroke="#fff" stroke-width="2.2"/><circle cx="11" cy="14.5" r="1.5" fill="#fff"/></svg>
      </div>
      <div class="time">4:21 PM</div>
      <div class="battery">
        <svg width="14" height="22" viewBox="0 0 14 22"><path d="M2 6l10 10-5 5V1l5 5L2 16" fill="none" stroke="#fff" stroke-width="1.6"/></svg>
        <span>22%</span>
        <svg width="48" height="22" viewBox="0 0 48 22"><rect x="1" y="2" width="42" height="18" rx="3" fill="none" stroke="#fff" stroke-width="2"/><rect x="4" y="5" width="9" height="12" fill="#fff"/><rect x="44" y="8" width="3" height="6" fill="#fff"/></svg>
      </div>
    </div>

    <main class="content">
      <div class="brand"><span class="brand-dot"></span><span class="brand-name">Brindleworth.com</span></div>
      <h1 class="headline">Want To <span class="earn">Earn</span> <span class="extra">Extra</span> <span class="money">Money?</span></h1>
      <p class="tagline">With Brindleworth.com. It's Easy As 1.2.3.</p>

      <div class="coin-art" role="img" aria-label="Glowing green coin illustration with a dollar sign"></div>

      <section class="panel steps">
        <div class="step one"><div class="step-bar">Register</div><div class="step-num">1</div></div>
        <div class="step two"><div class="step-bar">Earn &amp; Win Coins</div><div class="step-num">2</div></div>
        <div class="step three"><div class="step-bar">Reedem Coins</div><div class="step-num">3</div></div>
      </section>

      <section class="panel login">
        <div class="field user">
          <svg width="20" height="22" viewBox="0 0 20 22"><circle cx="10" cy="6" r="5" fill="var(--icon)"/><path d="M1 21a9 8 0 0 1 18 0z" fill="var(--icon)"/></svg>
          <span>Username@postlark.com</span>
        </div>
        <div class="field pass">
          <svg width="18" height="22" viewBox="0 0 18 22"><path d="M4 10V7a5 5 0 0 1 10 0v3" fill="none" stroke="var(--icon)" stroke-width="2.5"/><rect x="1" y="10" width="16" height="11" rx="1.5" fill="var(--icon)"/></svg>
          <span>Password</span>
        </div>
        <div class="login-row">
          <span class="login-btn">Login</span>
          <span class="forgot">Forgot my Password?</span>
        </div>
        <div class="social-btn"><span class="social-mark"></span><span>Login with Linkwave</span></div>
      </section>
    </main>
  </div>
</body>
</html>
```